Local Flower Farm Needs Business Card Design

I need business cards designed for a flower farm based in Eudora, Kansas.
Business Info:
We are a local cut flower farm located in Eudora, Kansas, founded by Corinne Haldwick. What started as a passion for agriculture and search for more joy in daily life has blossomed into a small business dedicated to providing the community with beautiful, fresh, and sustainable flowers. We specialize in local, seasonal blooms, ensuring that every petal reflects the care and dedication we pour into our craft. Our mission is to deliver the highest quality flowers directly to our customers through local farmers markets and to florists who share our commitment to sustainability. Join us in celebrating the beauty of nature, one bloom at a time!
Contact Details:
Corinne Haldwick
Owner
Phone 913-555-0147
Facebook: Rosalind Thorpe Gardens
Instagram: @RosalindThorpeGardens
Website: RosalindThorpeGardens.example
Target Market(s)
Wholesale to Florists and Direct to Consumer via Farmers Market
Industry/Entity Type
Florist, Farm
Contact Information for Business Card
Name, Contact Info, Logo
Look and feel
Each slider illustrates characteristics of the customer's brand and the style your logo design should communicate.

```html
<!DOCTYPE html>
<html lang="en">
<head>
<meta charset="utf-8">
<title>Rosalind Thorpe Gardens – Business Card</title>
<link href="https://fonts.googleapis.com/css2?family=Montserrat:wght@400;500;700&display=swap" rel="stylesheet">
<style>
  :root {
    --ink: #0b2a2e;
    --text: #1a1a1a;
    --paper: #ffffff;
    --backdrop: #e8e8e8;
    --ghost: #e4e4e4;
    --muted: #3a4a4c;
  }
  html, body {
    margin: 0;
    width: 1200px;
    height: 1108px;
    overflow: hidden;
    background: var(--backdrop);
    font-family: "Montserrat", sans-serif;
  }
  .card {
    position: absolute;
    background: var(--paper);
    overflow: hidden;
  }
  .card--front { left: 219px; top: 51px; width: 774px; height: 472px; }
  .card--back  { left: 217px; top: 568px; width: 776px; height: 456px; }

  .band {
    position: absolute;
    left: 0; top: 40px;
    width: 100%; height: 84px;
    background: var(--ink);
  }
  .badge {
    position: absolute;
    left: 80px; top: 15px;
    width: 124px; height: 124px;
    border-radius: 50%;
    background: var(--paper);
    box-sizing: border-box;
    border: 2px solid var(--ink);
    display: flex; align-items: center; justify-content: center;
    text-align: center;
    color: var(--ink);
    font-weight: 500;
    font-size: 13px;
    line-height: 1.25;
    letter-spacing: 0.5px;
  }
  .holder {
    position: absolute;
    right: 51px; top: 52px;
    text-align: right;
    color: var(--paper);
  }
  .holder__name { font-weight: 700; font-size: 29px; line-height: 1.1; }
  .holder__role { font-weight: 400; font-size: 18px; margin-top: 4px; }

  .ghost-mark {
    position: absolute;
    left: 509px; top: 210px;
    width: 210px;
    color: var(--ghost);
    font-weight: 500;
    font-size: 40px;
    line-height: 1.15;
  }

  .contacts {
    position: absolute;
    left: 42px; top: 327px;
    margin: 0; padding: 0;
    list-style: none;
    font-size: 18px;
    color: var(--text);
  }
  .contacts li {
    display: flex; align-items: center;
    height: 28.5px;
  }
  .contacts svg { width: 18px; height: 18px; margin-right: 8px; flex: none; }
  .dot { width: 14px; height: 14px; border-radius: 50%; background: var(--text); margin: 0 10px 0 2px; flex: none; }

  .address {
    position: absolute;
    left: 527px; top: 393px;
    font-size: 18px;
    line-height: 22px;
    color: var(--text);
  }

  .seal {
    position: absolute;
    left: 230px; top: 82px;
    width: 336px; height: 336px;
    border-radius: 50%;
    border: 2px solid var(--muted);
    box-sizing: border-box;
    display: flex; align-items: center; justify-content: center;
    text-align: center;
    color: var(--ink);
    font-weight: 500;
    font-size: 38px;
    line-height: 1.2;
    letter-spacing: 1px;
  }
</style>
</head>
<body>
  <section class="card card--front">
    <div class="band"></div>
    <div class="badge">Rosalind<br>Thorpe<br>Gardens</div>
    <div class="holder">
      <div class="holder__name">Corinne Haldwick</div>
      <div class="holder__role">Owner</div>
    </div>

    <div class="ghost-mark" aria-hidden="true">Rosalind Thorpe Gardens</div>

    <ul class="contacts">
      <li>
        <svg viewBox="0 0 24 24" aria-hidden="true"><path fill="#1a1a1a" d="M6.6 10.8a15.1 15.1 0 0 0 6.6 6.6l2.2-2.2a1 1 0 0 1 1-.25 11.4 11.4 0 0 0 3.6.57 1 1 0 0 1 1 1V20a1 1 0 0 1-1 1A17 17 0 0 1 3 4a1 1 0 0 1 1-1h3.5a1 1 0 0 1 1 1c0 1.25.2 2.45.57 3.57a1 1 0 0 1-.25 1z"/></svg>
        913-555-0147
      </li>
      <li><span class="dot"></span>Rosalind Thorpe Gardens</li>
      <li><span class="dot"></span>@RosalindThorpeGardens</li>
      <li>
        <svg viewBox="0 0 24 24" aria-hidden="true"><circle cx="12" cy="12" r="10" fill="#1a1a1a"/><path d="M2 12h20M12 2c3 3 3 17 0 20M12 2c-3 3-3 17 0 20" stroke="#fff" stroke-width="1.4" fill="none"/></svg>
        www.RosalindThorpeGardens.example
      </li>
    </ul>

    <div class="address">418 Meadowlark Ln, #112<br>Eudora, KS 660251</div>
  </section>

  <section class="card card--back">
    <div class="seal">Rosalind<br>Thorpe<br>Gardens</div>
  </section>
</body>
</html>
```